Brightmoor - a website to encourage people to spend time in nature

I have a squarespace site with some content on it but the squarespace template doesn't completely suit my needs, I keep fiddling with the template but actually I need some professional help to get it looking the way I want and with the right 'mood'.
The website is for "Brightmoor" - it will be a blog where I write about the importance of nature for good health. I also want to use the website to market services such as outdoor coaching, retreats and walking workshops.
This has been in my head for a LONG time and I currently only use instagram for micro-blogs but it's time for me to get this moving. I've previously engaged other designers on branding for it but they just didn't get it quite the way that I wanted it and I wasn't completely happy with the results. It's been a process for me as to what I want but in the meantime I just didn't come back to the design aspect of it now. I'm looking for a designer who understands the purpose of the website, the ethos and can help me realise this into a design that's clean, clear and simple.

Please note that I have a domain (brightmoor.org) and a lot of content drafted on squarespace already. I have published it with password protection - password is brightmoor2020 - it still has some of the original template on it, but does have some content. Don't take it as anything to follow in particular, i am looking for fresh eyes and fresh ideas.

Target Market(s)

There are three main groups that I want to target - people who are suffering from stress and anxiety, people who treat them and parents who want to get their kids outside (thereby preventing stress and anxiety)

Contact Information for Business Card

Joan Petrie
Brightmoor
Telephone +44 7700 900417
brightmoor@mailvane.com

Logo Text

Brightmoor - if that. I have an idea that the logo should have a leaf on it somewhere, or maybe just be a leaf.

Coding

Coded - Design and coding required

Number of Pages Required

5+ page

Font styles to use
Serif
Sans Serif

Colors
add136
33b8a4
34a6d7
3377b5

Requirements
Must have
• Space for lots of images. The ability for me to edit the pages if I need to. Be user friendly. Look beautiful.
• For an idea of the images I use and the content I'm interested in writing about have a look at @brightmoor on instagram.
• That pop up about cookies so I am complying with data laws.
Should not have
• Must not be too 'busy' I'd like to avoid too much movement.

```html
<!DOCTYPE html>
<html lang="en">
<head>
<meta charset="utf-8">
<title>Brightmoor — Time in nature to feel better</title>
<link rel="stylesheet" href="https://fonts.googleapis.com/css2?family=Bodoni+Moda:wght@400;500;700&family=Oswald:wght@300&family=Poppins:wght@400&display=swap">
<style>
:root{
  --ink:#111111;
  --white:#ffffff;
  --mist:#dfe8ec;
  --mist-deep:#a9bcbe;
  --paper:#efefef;
  --subscribe-bg:#ebebeb;
  --teal-dark:#0d4f55;
  --teal:#1f8a8c;
  --rock:#2f3a33;
  --muted:#555b5e;
  --line:#9aa3a6;
}
*{margin:0;padding:0;box-sizing:border-box}
html,body{width:1200px;height:3640px;overflow:hidden;background:var(--white)}
body{font-family:"Poppins",sans-serif;color:var(--ink)}
.page{position:relative;width:1200px;height:3640px;overflow:hidden}
.abs{position:absolute}
.serif{font-family:"Bodoni Moda",serif}
.wordmark{font-family:"Oswald",sans-serif;font-weight:300;letter-spacing:12px;color:var(--white)}

/* header */
.site-header{left:0;top:0;width:1200px;height:105px;background:var(--ink)}
.menu-btn{left:142px;top:32px;width:50px;height:50px;border-radius:50%;background:var(--white)}
.menu-btn span{position:absolute;left:15px;width:20px;height:3px;border-radius:2px;background:var(--ink)}
.icon-ring{top:32px;width:50px;height:50px;border-radius:50%;border:2px solid var(--white)}
.header-logo{left:0;top:22px;width:1200px;text-align:center;font-size:50px;line-height:60px}

/* hero */
.hero-photo{left:0;top:105px;width:1200px;height:760px;
  background:linear-gradient(180deg,var(--rock) 0%,#32463d 28%,#1d6b6c 48%,var(--teal) 62%,var(--teal-dark) 100%)}
.hero-rule{left:395px;top:294px;width:417px;height:3px;background:var(--white);border-radius:50%}
.hero-title{left:0;top:325px;width:1200px;text-align:center;font-size:86px;font-weight:500;color:var(--white);letter-spacing:1px}
.hero-tagline{left:0;top:440px;width:1200px;text-align:center;font-size:21px;letter-spacing:2px;color:var(--white)}
.pill{display:flex;align-items:center;justify-content:space-between;border-radius:30px;font-family:"Bodoni Moda",serif;text-transform:uppercase;letter-spacing:1px}
.pill i{display:block;border-radius:50%;background:var(--ink);position:relative}
.pill i::after{content:"»";position:absolute;inset:0;color:var(--white);font-style:normal;font-size:14px;line-height:18px;text-align:center}
.hero-btn{left:514px;top:516px;width:155px;height:44px;background:var(--white);padding:0 14px 0 20px;font-size:12px}
.hero-btn i{width:20px;height:20px}
.dot{top:599px;width:16px;height:16px;border-radius:50%;border:2px solid var(--white)}
.dot.active{width:20px;height:20px;top:597px;background:radial-gradient(circle,var(--white) 55%,transparent 60%);}

/* about */
.about-title{left:188px;top:875px;font-size:42px;font-weight:500;letter-spacing:1px}
.about-rule{left:188px;top:935px;width:372px;height:1px;background:var(--line)}
.about-text{left:186px;top:956px;width:378px;font-size:12.6px;line-height:18px;text-align:justify;color:#222}
.outline-btn{height:36px;border:1.5px solid var(--ink);background:transparent;padding:0 8px 0 18px;font-size:9.5px}
.outline-btn i{width:17px;height:17px}
.outline-btn i::after{font-size:11px;line-height:16px}
.about-btn{left:187px;top:1127px;width:127px}
.about-photo{left:630px;top:842px;width:408px;height:408px;border-radius:50%;
  background:linear-gradient(180deg,#6f7a83 0%,#a8a59a 45%,#d9c9a6 62%,#6d6f63 100%)}

/* gallery */
.gallery{left:0;top:1279px;width:1200px;height:865px;background:var(--paper)}
.section-title{left:0;width:1200px;text-align:center;font-size:42px;font-weight:500;letter-spacing:1px}
.section-rule{left:570px;width:60px;height:2px;background:var(--ink)}
.tile{display:block}
.tile-plus{left:567px;top:1810px;width:54px;height:54px;border:1.5px solid var(--white)}
.tile-plus::before,.tile-plus::after{content:"";position:absolute;background:var(--white);left:50%;top:50%;transform:translate(-50%,-50%)}
.tile-plus::before{width:24px;height:2px}
.tile-plus::after{width:2px;height:24px}
.gallery-btn{left:540px;top:2028px;width:121px}

/* blog */
.blog{left:0;top:2144px;width:1200px;height:840px;
  background:linear-gradient(180deg,#e6ecef 0%,#cfdbe2 28%,#dfe7ec 45%,#e8eef1 70%,#eef1f2 100%)}
.card{top:2339px;width:286px;height:380px;background:var(--white);box-shadow:0 2px 8px rgba(0,0,0,.12)}
.card-photo{position:absolute;left:0;top:0;width:286px;height:191px}
.card-date{position:absolute;left:2px;top:146px;width:49px;height:45px;background:var(--ink);color:var(--white);font-family:"Bodoni Moda",serif;padding:5px 0 0 9px;line-height:1}
.card-date small{display:block;font-size:10px}
.card-date b{display:block;font-size:18px;font-weight:500}
.card-title{position:absolute;left:25px;top:212px;font-family:"Bodoni Moda",serif;font-size:13.5px;letter-spacing:1px}
.card-text{position:absolute;left:25px;top:237px;width:245px;font-size:10.6px;line-height:16.5px;color:#333}
.card-btn{position:absolute;left:25px;top:327px;height:29px;padding:0 10px;border:1px solid var(--ink);font-family:"Bodoni Moda",serif;font-size:10px;letter-spacing:1px;line-height:27px}
.card-btn.solid{background:var(--ink);color:var(--white)}
.pager{top:2758px;width:34px;height:5px;background:#8a8f92}
.pager.active{background:var(--ink)}

/* subscribe */
.subscribe{left:0;top:2760px;width:1200px;height:563px;background:var(--subscribe-bg)}
.contact-icon{left:177px;width:38px;height:38px;border-radius:50%;background:var(--ink)}
.contact-label{left:232px;font-family:"Bodoni Moda",serif;font-size:19px}
.contact-value{left:232px;font-family:"Bodoni Moda",serif;font-size:12px;color:#333}
.field{height:34px;border:1.5px solid #777;font-family:"Bodoni Moda",serif;font-size:10px;letter-spacing:1px;padding-left:12px;line-height:31px;color:#333}
.subscribe-btn{left:563px;top:3206px;width:450px;height:41px;background:var(--ink);color:var(--white);font-family:"Bodoni Moda",serif;font-size:16px;letter-spacing:1px;text-align:center;line-height:41px}

/* footer */
.site-footer{left:0;top:3322px;width:1200px;height:318px;background:var(--ink)}
.footer-logo{left:0;top:3398px;width:1200px;text-align:center;font-size:48px;line-height:60px}
.footer-rule{left:424px;width:352px;height:1px;background:#555}
.follow{left:0;top:3498px;width:1200px;text-align:center;font-family:"Bodoni Moda",serif;color:var(--white);font-size:17px}
.follow span{display:inline-block;width:24px;height:24px;border-radius:50%;border:2px solid var(--white);vertical-align:middle;margin-left:10px}
.copyright{left:0;top:3558px;width:1200px;text-align:center;font-family:"Bodoni Moda",serif;color:#ccc;font-size:11px}
</style>
</head>
<body>
<div class="page">

  <!-- header -->
  <header class="site-header abs">
    <div class="menu-btn abs"><span style="top:17px"></span><span style="top:24px"></span><span style="top:31px"></span></div>
    <div class="header-logo wordmark abs">BRIGHTMOOR</div>
    <div class="icon-ring abs" style="left:922px" aria-label="Social profile"></div>
    <div class="icon-ring abs" style="left:993px" aria-label="Search">
      <svg width="46" height="46" viewBox="0 0 46 46"><circle cx="21" cy="21" r="8" fill="none" stroke="#fff" stroke-width="2.2"/><line x1="27" y1="27" x2="32" y2="32" stroke="#fff" stroke-width="2.4" stroke-linecap="round"/></svg>
    </div>
  </header>

  <!-- hero -->
  <section>
    <div class="hero-photo abs" role="img" aria-label="Woman in a wooden boat on a turquoise lake below forested limestone cliffs"></div>
    <div class="hero-rule abs"></div>
    <h1 class="hero-title serif abs">BRIGHTMOOR</h1>
    <p class="hero-tagline abs">The practice of spending time in nature to feel better.</p>
    <div class="hero-btn pill abs">Read more<i></i></div>
    <div class="dot abs" style="left:548px"></div>
    <div class="dot active abs" style="left:575px"></div>
    <div class="dot abs" style="left:607px"></div>
    <div class="dot abs" style="left:637px"></div>
    <svg class="abs" style="left:0;top:660px" width="1200" height="630" viewBox="0 0 1200 630">
      <path d="M0 118 C120 160 240 150 380 80 C470 30 560 0 640 30 C760 90 830 200 960 205 C1060 205 1150 180 1200 170 L1200 630 L0 630 Z" fill="#b7c7c9"/>
      <path d="M0 140 C140 175 260 150 400 85 C490 45 540 25 600 45 C720 100 800 210 940 210 C1050 210 1140 195 1200 190 L1200 630 L0 630 Z" fill="var(--mist)"/>
    </svg>
  </section>

  <!-- about -->
  <section>
    <h2 class="about-title serif abs">ABOUT US</h2>
    <div class="about-rule abs"></div>
    <p class="about-text abs">Welcome to Brightmoor. An investigation of how spending time in nature helps you to feel better - physically, mentally, spiritually. This started as a personal journey to counteract the effect of too many hours in artificially lit offices, too much stress and too little connection to the natural world. It became something of a mission. To help others re-find their connection to the natural world, and in the process, live better and feel better.</p>
    <div class="about-btn outline-btn pill abs">View more<i></i></div>
    <div class="about-photo abs" role="img" aria-label="Hiker with a large backpack standing on a hilltop under a cloudy sky"></div>
  </section>

  <!-- gallery -->
  <section>
    <div class="gallery abs"></div>
    <h2 class="section-title serif abs" style="top:1337px">PHOTO GALLERY</h2>
    <div class="section-rule abs" style="top:1398px"></div>
    <div class="tile abs" style="left:143px;top:1432px;width:294px;height:315px;background:linear-gradient(135deg,#c93a6b,#f2a9c0 50%,#d9577f)" role="img" aria-label="Pink cherry blossom"></div>
    <div class="tile abs" style="left:448px;top:1432px;width:293px;height:237px;background:linear-gradient(135deg,#2f5a2c,#4f8a3e 50%,#24431f)" role="img" aria-label="Ladybird on green leaves"></div>
    <div class="tile abs" style="left:752px;top:1432px;width:293px;height:315px;background:linear-gradient(180deg,#7eb3e3 0%,#9cc4e0 18%,#3b3c3c 22%,#2c2b2a 100%)" role="img" aria-label="Small dog on a dark sandy beach with a long shadow"></div>
    <div class="tile abs" style="left:143px;top:1757px;width:294px;height:237px;background:linear-gradient(180deg,#8b9460,#6f7a45 55%,#a3957f)" role="img" aria-label="Woodland path between trees"></div>
    <div class="tile abs" style="left:448px;top:1679px;width:293px;height:315px;background:linear-gradient(180deg,#5a5c60,#6a6d72 60%,#4b4a48)" role="img" aria-label="Child looking out over the sea"></div>
    <div class="tile-plus abs"></div>
    <div class="tile abs" style="left:752px;top:1757px;width:293px;height:237px;background:linear-gradient(180deg,#6f7d4c,#4e5b33 55%,#5b4ea6)" role="img" aria-label="Bluebells on a forest floor"></div>
    <div class="gallery-btn outline-btn pill abs">View all<i></i></div>
  </section>

  <!-- blog -->
  <section>
    <div class="blog abs" role="img" aria-label="Pale misty mountain range reflected in a lake"></div>
    <h2 class="section-title serif abs" style="top:2237px">OUR BLOG</h2>
    <div class="section-rule abs" style="top:2297px"></div>

    <article class="card abs" style="left:143px">
      <div class="card-photo" role="img" aria-label="Person in a meadow of wildflowers" style="background:linear-gradient(180deg,#c7d3df 0%,#9fb3c6 30%,#5d8a3a 55%,#b84a2a 80%,#e0c23a)"></div>
      <div class="card-date"><small>AUG</small><b>18</b></div>
      <h3 class="card-title">ON THE VERGE</h3>
      <p class="card-text">Sometimes it's just the simple things. You can be in a mix of complexity and it'll be something simple that will jolt you back to the now...</p>
      <div class="card-btn">READ MORE »</div>
    </article>

    <article class="card abs" style="left:452px">
      <div class="card-photo" role="img" aria-label="Blue sky with scattered clouds" style="background:linear-gradient(160deg,#4d6b96,#a9b8c9 45%,#5c7aa3 75%,#33486b)"></div>
      <div class="card-date"><small>APR</small><b>30</b></div>
      <h3 class="card-title">SKYTIME OVER SCREENTIME</h3>
      <p class="card-text">This is the defining challenge of parenting in the 21st Century. It's a recurring theme in conversations I have with other parents, it's on news bulletins...</p>
      <div class="card-btn solid">READ MORE »</div>
    </article>

    <article class="card abs" style="left:760px">
      <div class="card-photo" role="img" aria-label="Bird nest in a snowy rock face" style="background:linear-gradient(180deg,#e4e4e4,#cfcfcf 45%,#5a4a3f 62%,#dcdcdc 78%,#ececec)"></div>
      <div class="card-date"><small>JUN</small><b>17</b></div>
      <h3 class="card-title">NOTES FROM THE NEST</h3>
      <p class="card-text">As I've spent more time in nature over the last couple of years, I've started to see the lessons we can take from it, lessons writ large. There are two in particular...</p>
      <div class="card-btn">READ MORE »</div>
    </article>

    <div class="pager abs" style="left:527px"></div>
    <div class="pager active abs" style="left:579px"></div>
    <div class="pager abs" style="left:625px"></div>
  </section>

  <!-- subscribe -->
  <section>
    <div class="subscribe abs"></div>
    <svg class="abs" style="left:0;top:2760px" width="1200" height="200" viewBox="0 0 1200 200">
      <path d="M0 0 L1200 0 L1200 0 C1120 0 1060 20 1000 70 C920 130 820 130 720 110 C560 80 400 150 250 140 C150 132 90 100 40 110 C20 114 8 120 0 124 Z" fill="#e8eef1"/>
      <path d="M0 124 C30 105 90 100 150 125 C230 160 300 200 360 190 C300 170 220 110 120 95 C60 88 20 100 0 110 Z" fill="#a9bcbe"/>
      <path d="M1000 70 C1060 20 1120 0 1200 0 L1200 10 C1120 8 1060 35 1010 85 C980 110 960 118 940 120 C960 110 980 90 1000 70 Z" fill="#a9bcbe"/>
    </svg>
    <h2 class="section-title serif abs" style="top:3022px">SUBSCRIBE US</h2>

    <div class="contact-icon abs" style="top:3129px" aria-label="Phone">
      <svg width="38" height="38" viewBox="0 0 38 38"><path d="M13 10 L17 10 L18 15 L15.5 17 C16.8 19.8 18.4 21.4 21 22.5 L23 20 L28 21 L28 25 C28 26.5 26.8 27.6 25 27.4 C17.4 26.5 11.5 20.6 10.6 13 C10.4 11.2 11.5 10 13 10 Z" fill="#fff"/></svg>
    </div>
    <div class="contact-label abs" style="top:3124px">Call Us:</div>
    <div class="contact-value abs" style="top:3151px">+44 7700 900417</div>

    <div class="contact-icon abs" style="top:3192px" aria-label="Email">
      <svg width="38" height="38" viewBox="0 0 38 38"><circle cx="19" cy="19" r="11" fill="none" stroke="#fff" stroke-width="2"/><text x="19" y="24" text-anchor="middle" fill="#fff" font-size="15" font-family="Poppins,sans-serif">@</text></svg>
    </div>
    <div class="contact-label abs" style="top:3189px">Mail Us:</div>
    <div class="contact-value abs" style="top:3216px">brightmoor@mailvane.com</div>

    <div class="field abs" style="left:563px;top:3117px;width:221px">FIRST NAME</div>
    <div class="field abs" style="left:793px;top:3117px;width:221px">LAST NAME</div>
    <div class="field abs" style="left:563px;top:3161px;width:450px">EMAIL ADDRESS</div>
    <div class="subscribe-btn abs">SUBSCRIBE</div>
  </section>

  <!-- footer -->
  <footer>
    <div class="site-footer abs"></div>
    <div class="footer-logo wordmark abs">BRIGHTMOOR</div>
    <div class="footer-rule abs" style="top:3490px"></div>
    <div class="follow abs">Follow Us On:<span></span></div>
    <div class="footer-rule abs" style="top:3534px"></div>
    <div class="copyright abs">© Copyright 2016. All Rights Reserved</div>
  </footer>

</div>
</body>
</html>
```